High-end construction company needs a business card design

We need a modern looking business card that draws people in, is memorable and looks so good people will want to sick it on their fridges.
On the first side what is needed are:
Logo
My name - Tomasz Brelwik
Title - Managing Director
Website - www.varkelt.co.uk
Email - tomasz@varkelt.co.uk
Telephone - 020 5194 6281
Mobile - 07845139072
On the back side was is needed is a list of all the services we provide:
-Kitchen Renovations
-Bathroom Renovations
-House Renovations
-Garage Conversions
-Extensions
-Loft Conversions
-Conservatories
-Carpentry
-Tiling
-Electrical
-Plumbing & Heating
-Bricklaying
-Landscaping
-Decorating
-Plastering
We would like the colours to be the same shades as on the logo with grey or black for the words.
Target Market(s)
Anyone who needs building work done
Contact Information for Business Card
This business card is for a construction company which strives to deliver excellent service and quality.
The look and feel of the card should represent this.
Requirements
Must have
- On the first side what is needed are:
Logo
My name - Tomasz Brelwik
Title - Managing Director
Website - www.varkelt.co.uk
Email - tomasz@varkelt.co.uk
Telephone - 020 5194 6281
Mobile - 07845139072
Nice to have
- Cool looking features

```html
<!DOCTYPE html>
<html lang="en">
<head>
<meta charset="utf-8">
<title>Varkelt Construction Ltd – Business Card</title>
<link rel="stylesheet" href="https://fonts.googleapis.com/css2?family=Exo+2:wght@400;600;700&display=swap">
<style>
  :root {
    --page-bg: #8d8d8d;
    --card-white: #ffffff;
    --green-light: #6cbd45;
    --green-dark: #4b8e40;
    --text-grey: #4a4a4a;
    --text-white: #ffffff;
  }
  * { box-sizing: border-box; margin: 0; padding: 0; }
  html, body {
    width: 1125px; height: 1200px; overflow: hidden;
    background: var(--page-bg);
    font-family: "Exo 2", Arial, sans-serif;
  }
  .canvas { position: relative; width: 1125px; height: 1200px; }

  .card { position: absolute; left: 171px; width: 826px; height: 471px; overflow: hidden; }

  /* Front */
  .card-front { top: 106px; background: var(--card-white); }
  .brand {
    position: absolute; left: 190px; top: 300px; width: 220px;
    color: var(--green-light); font-weight: 700; text-align: center; line-height: 1;
  }
  .brand-name { font-size: 52px; letter-spacing: 1px; text-transform: uppercase; }
  .brand-sub { font-size: 14.5px; letter-spacing: 2.4px; text-transform: uppercase; margin-top: 6px; }
  .divider {
    position: absolute; left: 433px; top: 162px; width: 1px; height: 148px;
    background: var(--green-light);
  }
  .person { position: absolute; left: 460px; top: 161px; }
  .person-name { font-size: 27px; font-weight: 600; color: var(--green-light); line-height: 1.1; }
  .person-title { font-size: 17px; color: var(--green-dark); margin-top: 1px; }
  .contacts { list-style: none; margin-top: 24px; }
  .contact {
    display: flex; align-items: center; gap: 10px;
    font-size: 18px; color: var(--text-grey); height: 23.5px;
  }
  .contact-email { font-size: 16.5px; }
  .contact svg { width: 14px; height: 14px; fill: var(--green-light); flex: none; }
  .accent-bar {
    position: absolute; left: 0; right: 0; bottom: 0; height: 11px;
    background: var(--green-light);
  }
  .web-tab {
    position: absolute; left: 488px; bottom: 0; width: 245px; height: 39px;
    background: var(--green-dark); color: var(--text-white);
    font-size: 19px; letter-spacing: 1px; text-transform: uppercase;
    display: flex; align-items: center; justify-content: center;
    box-shadow: 0 0 0 3px var(--card-white);
  }

  /* Back */
  .card-back { top: 640px; background: var(--green-dark); color: var(--text-white); }
  .brand-large {
    position: absolute; left: 0; right: 0; top: 150px; text-align: center;
    font-size: 90px; font-weight: 700; letter-spacing: 6px; text-transform: uppercase; line-height: 1;
  }
  .ground-line {
    position: absolute; left: 142px; top: 277px; width: 518px; height: 3px;
    background: var(--text-white);
  }
  .services {
    position: absolute; left: 0; right: 0; top: 313px; text-align: center;
    font-size: 17.5px; line-height: 23.5px;
  }
  .tick { margin: 0 3px; }
</style>
</head>
<body>
<main class="canvas">

  <section class="card card-front" aria-label="Business card front">
    <div class="brand">
      <div class="brand-name">Varkelt</div>
      <div class="brand-sub">Construction Ltd</div>
    </div>
    <div class="divider"></div>
    <div class="person">
      <h1 class="person-name">Tomasz Brelwik</h1>
      <p class="person-title">Managing Director</p>
      <ul class="contacts">
        <li class="contact">
          <svg viewBox="0 0 24 24" aria-hidden="true"><path d="M6.6 10.8a15.1 15.1 0 0 0 6.6 6.6l2.2-2.2c.3-.3.7-.4 1-.2 1.1.4 2.3.6 3.6.6.6 0 1 .4 1 1V20c0 .6-.4 1-1 1A17 17 0 0 1 3 4c0-.6.4-1 1-1h3.5c.6 0 1 .4 1 1 0 1.3.2 2.5.6 3.6.1.3 0 .7-.2 1z"/></svg>
          020 5194 6281
        </li>
        <li class="contact">
          <svg viewBox="0 0 24 24" aria-hidden="true"><path d="M7 1h10a2 2 0 0 1 2 2v18a2 2 0 0 1-2 2H7a2 2 0 0 1-2-2V3a2 2 0 0 1 2-2zm0 3v14h10V4zm5 15.5a1.2 1.2 0 1 0 0 2.4 1.2 1.2 0 0 0 0-2.4z"/></svg>
          07845139072
        </li>
        <li class="contact contact-email">
          <svg viewBox="0 0 24 24" aria-hidden="true"><path d="M2 6h20v12H2zm2 1.5 8 5.5 8-5.5V7H4z"/></svg>
          tomasz@varkelt.co.uk
        </li>
      </ul>
    </div>
    <div class="accent-bar"></div>
    <div class="web-tab">www.varkelt.co.uk</div>
  </section>

  <section class="card card-back" aria-label="Business card back">
    <div class="brand-large">Varkelt</div>
    <div class="ground-line"></div>
    <p class="services">
      Kitchen Renovations<span class="tick">✓</span>Bathroom Renovations<span class="tick">✓</span>House Renovations<br>
      Garage Conversions<span class="tick">✓</span>Extensions<span class="tick">✓</span>Loft Conversions<span class="tick">✓</span>Conservatories<br>
      Carpentry<span class="tick">✓</span>Tiling<span class="tick">✓</span>Electrical<span class="tick">✓</span>Plumbing &amp; Heating<span class="tick">✓</span>Bricklaying<br>
      Landscaping<span class="tick">✓</span>Decorating<span class="tick">✓</span>Plastering
    </p>
  </section>

</main>
</body>
</html>
```